Need a small Brochure Designing for a High Tech LED Spotlight

This is an expensive product and the best of it's kind in the world, so it needs to be marketed to intelligent, forward thinking people who appreciate and pay for excellent design and innovation. The type of people who buy Quince products i guess. It needs to be clean. The colours do not need to be in keep with our website, but our logo does need to be on the brochure. I have attached a dcoument with all the text, the order the text goes in and an idea of how i want the first page to look. All images and logos have been attached too.

Target Market(s)

This is aimed at people with high disposible incomes who spend money on the best designed products and the latest technology. The type of people who buy Quince products.

Industry/Entity Type

Product

Requirements
Must have
• The work needs to be editable by us using indesign

The pages need to be A5. I'm not sure how many pages the brochure needs to be as it does need to be clean and be spaced out well. On the file that contains the text i've indicated that 8 pages would be good.

The logos i attached - 1) Brava Product Design Award, 2) K Technology Award, 3) Tall Oak Design Award and 4) Keen Form Award all need to be at the bottom of the front page, quite small, but still able to see them well.

- Needs to have a QR code so that smart phones can scan the code and be taken to a zen pier clip - QR code is attached.
- Needs to have Tumbolt Icon - @BrightNookCo
Nice to have
• Nice to remind customers on each page that the product has a 5 year Warranty and we have a 365 day Returns Policy.

```html
<!DOCTYPE html>
<html lang="en">
<head>
<meta charset="utf-8">
<title>N7 LED Spot – Testimonials</title>
<link rel="stylesheet" href="https://fonts.googleapis.com/css2?family=Questrial&family=Raleway:wght@200;700&display=swap">
<style>
  :root {
    --page: #f8f6f5;
    --panel: #f5eeed;
    --band: #a9aaac;
    --ink: #3a3a3a;
    --soft: #a3a3a3;
    --rule: #bdbdbd;
    --photo-top: #f1f0ee;
    --photo-mid: #e2dcd6;
    --photo-floor: #c99c72;
  }
  * { box-sizing: border-box; margin: 0; padding: 0; }
  html, body { width: 827px; height: 1200px; overflow: hidden; background: #fff; }
  body { position: relative; font-family: "Questrial", sans-serif; color: var(--ink); }

  .testimonial-page { position: absolute; left: 0; top: 0; width: 827px; height: 586px; background: var(--page); }
  .section-title { position: absolute; left: 37px; top: 42px; font-family: "Raleway", sans-serif; font-weight: 700; font-size: 10px; }
  .quote { position: absolute; font-size: 10.9px; line-height: 12px; }
  .quote .who { display: block; margin-bottom: 10px; }
  .quote p + p { margin-top: 10px; }
  .col-left { left: 37px; width: 345px; }
  .col-right { left: 449px; width: 345px; }

  .rating { position: absolute; right: 36px; top: 459px; text-align: right; font-family: "Raleway", sans-serif; font-weight: 200; font-size: 25px; line-height: 28px; color: var(--soft); }
  .policy-note { position: absolute; font-size: 6px; color: var(--ink); text-align: center; }
  .policy-top { left: 414px; width: 413px; top: 557px; }

  .divider-band { position: absolute; left: 0; top: 586px; width: 827px; height: 26px; background: var(--band); }

  .showcase-page { position: absolute; left: 0; top: 612px; width: 827px; height: 584px; background: #fff; }
  .interior-photo { position: absolute; left: 0; top: 35px; width: 414px; height: 516px;
    background: linear-gradient(180deg, var(--photo-top) 0%, var(--photo-mid) 55%, var(--photo-floor) 72%, #b98a5f 100%); }
  .brand-panel { position: absolute; left: 414px; top: 0; width: 413px; height: 584px; background: var(--panel); }
  .brand-intro { position: absolute; left: 54px; top: 74px; width: 330px; font-size: 10.9px; line-height: 12px; }
  .brand-name { position: absolute; display: flex; align-items: center; gap: 7px; transform: translateX(-50%); font-size: 15px; color: var(--ink); white-space: nowrap; }
  .brand-name .dot { width: 12px; height: 12px; border-radius: 50%; background: var(--ink); }
  .policy-bottom { left: 0; width: 413px; top: 556px; }
  .page-edge { position: absolute; left: 0; top: 1196px; width: 827px; height: 4px; background: var(--rule); }
</style>
</head>
<body>
  <section class="testimonial-page">
    <h2 class="section-title">Testimonials:</h2>

    <div class="quote col-left" style="top:81px">
      <span class="who">LED Reviewer &amp; Blogger Jon:</span>
      <p>It's an incredibly impressive product. When you see and hold the product it oozes quality.</p>
      <p>The quality of the light was something else and it really made everything in the flat seem clearer. Our wine glasses looked brand new under these spots. Backed up with a 5 year warranty and a believable 40,000 hour lifespan (about 18 years) then it's certainly the product I would buy in a heart beat if my name began with Emir or ended in Petrovsky.</p>
    </div>

    <div class="quote col-left" style="top:245px">
      <span class="who">Adrian:</span>
      <p>The electrician who installed the lights compared them to a regular 50 watt light and we both agreed the light quality and colour was superior on the N7. A more energy efficient light and a better quality light, a win, win situation.</p>
    </div>

    <div class="quote col-left" style="top:351px">
      <span class="who">Simon:</span>
      <p>Once fitted they were more than I expected, brilliantly bright, but not too harsh , as I had ordered the warm white I cannot recommend them enough, they're great.</p>
    </div>

    <div class="quote col-left" style="top:445px">
      <span class="who">Matt:</span>
      <p>When you see the results, the light is incredible. The 135 degree beam angle fills my room much better than the previous 60 degree, there's very few (if any) dark spots now. I plumped for the "daytime" (natural white) colour, it does exactly as described, at midnight with the lights on it could be mistaken for noon – very, very impressed.</p>
    </div>

    <div class="quote col-right" style="top:92px">
      <span class="who">Cris :</span>
      <p>A superb spotlight that does all the seller says it does. An incredible amount of light for such a low wattage.</p>
    </div>

    <div class="quote col-right" style="top:174px">
      <span class="who">Ryan:</span>
      <p>I own a large apartment in Chelsea on the river and was sick and tired of having to replace blown halogens all the time. I believe in investing in the best quality products possible and the N7 7w LED Spot is certainly that. The product is exceptionally well designed, produces a light quality that is a vast improvement on my old halogens and I can control the lighting using the existing Tavo system. The 1 year returns period really hammers home how much the company believes in the product.</p>
    </div>

    <div class="quote col-right" style="top:327px">
      <span class="who">Dave at Marlow Builders:</span>
      <p>I would like to compliment you and your team at Bright Nook. Every question I asked, you responded to in a very professional way. The quality of your product is first class including delivery. All in all I have been extremely impressed and would have no hesitation in using you and your team again.</p>
    </div>

    <p class="rating">Customers who have bought<br>this product rate it at 96%</p>
    <p class="policy-note policy-top">This product has a 5 Year Warranty and 365 Day Return Policy</p>
  </section>

  <div class="divider-band"></div>

  <section class="showcase-page">
    <div class="interior-photo" role="img" aria-label="Bright open-plan kitchen and living room lit by recessed LED spotlights, with pendant lamps over a white island and a light timber floor"></div>

    <div class="brand-panel">
      <p class="brand-intro">As well as supplying lighting designers and Architects across Europe the following prestigious brands have also used this LED Spotlight Product.</p>

      <div class="brand-name" style="left:131px;top:230px"><span class="dot"></span>Haruden</div>
      <div class="brand-name" style="left:286px;top:230px"><span class="dot"></span>Lorvane</div>
      <div class="brand-name" style="left:131px;top:365px"><span class="dot"></span>Meridian Motors</div>
      <div class="brand-name" style="left:286px;top:365px"><span class="dot"></span>The Carrow Hotel</div>
      <div class="brand-name" style="left:206px;top:452px"><span class="dot"></span>Grovemart</div>

      <p class="policy-note policy-bottom">This product has a 5 Year Warranty and 365 Day Return Policy</p>
    </div>
  </section>

  <div class="page-edge"></div>
</body>
</html>
```